Post storm repair flyer

looking for an eye catching 6x9 postcard to send out to single family home owners advertising a "Post Storm Repair Special" explaining that after the recent hurricanes its very important to have your roof checked and any repairs fixed right away before they become a bigger more costly problem and that even though your home wasn't directly hit by the storm the high wind gust could've cause unseen damage.
offer $200 off any repair *some rules may apply
Crest Roofing
877.512.DUNE
www.DuneRoofingco.example

```html
<!DOCTYPE html>
<html lang="en">
<head>
<meta charset="utf-8">
<title>Crest Roofing – Post Storm Repair Special Postcard</title>
<link rel="stylesheet" href="https://fonts.googleapis.com/css2?family=Montserrat:wght@400;500;600;700;800&display=swap">
<style>
  :root {
    --page-bg: #ebe8e3;
    --card-bg: #e3e3e3;
    --mid-grey: #b4b4b4;
    --brand-yellow: #ffd000;
    --ink: #111111;
    --body-ink: #2a2a2a;
    --sub-ink: #444444;
    --offer-red: #e8141b;
    --photo-sky: #9fb4c4;
    --photo-roof: #5d534d;
    --white: #ffffff;
    --rule: #b9b9b9;
  }
  * { margin: 0; padding: 0; box-sizing: border-box; }
  html, body { width: 1200px; height: 1086px; overflow: hidden; }
  body {
    background: var(--page-bg);
    font-family: "Montserrat", sans-serif;
    position: relative;
  }
  .postcard {
    position: absolute;
    left: 250px;
    width: 699px;
    height: 472px;
    box-shadow: 0 6px 16px rgba(0,0,0,0.18);
  }
  .postcard--front { top: 62px; }
  .postcard--back { top: 573px; }
  .postcard svg { display: block; width: 100%; height: 100%; }
  .headline { font-family: "Montserrat", sans-serif; font-weight: 800; fill: var(--ink); }
  .subline { font-family: "Montserrat", sans-serif; font-weight: 600; fill: var(--sub-ink); }
  .phone-number { font-family: "Montserrat", sans-serif; font-weight: 700; fill: var(--white); letter-spacing: 1px; }
  .brand-name { font-family: "Montserrat", sans-serif; font-weight: 600; fill: var(--ink); letter-spacing: 1px; }
  .badge-text { font-family: "Montserrat", sans-serif; font-weight: 700; fill: var(--ink); }
  .badge-offer { font-family: "Montserrat", sans-serif; font-weight: 800; fill: var(--offer-red); }
  .badge-fine { font-family: "Montserrat", sans-serif; font-weight: 400; font-style: italic; fill: var(--ink); }
  .back-heading { font-family: "Montserrat", sans-serif; font-weight: 700; fill: var(--ink); }
  .back-copy { font-family: "Montserrat", sans-serif; font-weight: 500; fill: var(--body-ink); }
</style>
</head>
<body>

<!-- Front of postcard -->
<section class="postcard postcard--front" aria-label="Postcard front">
  <svg viewBox="0 0 873 590" xmlns="http://www.w3.org/2000/svg">
    <defs>
      <linearGradient id="roofPhotoFront" x1="0" y1="0" x2="0" y2="1">
        <stop offset="0" stop-color="#b3c4d0"/>
        <stop offset="0.35" stop-color="#8a949a"/>
        <stop offset="1" stop-color="#5a4f49"/>
      </linearGradient>
    </defs>
    <rect class="card-base" width="873" height="590" fill="var(--card-bg)"/>
    <polygon class="accent-stripe" points="0,55 250,195 585,0 612,0 262,212 0,72" fill="var(--mid-grey)"/>
    <polygon class="header-yellow" points="0,0 585,0 250,195 0,55" fill="var(--brand-yellow)"/>
    <g role="img" aria-label="Photo of two roofers in hard hats repairing shingles on a roof">
      <polygon points="612,0 873,0 873,240 600,398 262,212" fill="url(#roofPhotoFront)"/>
    </g>
    <polygon class="offer-panel" points="600,398 873,240 873,590 600,590" fill="var(--mid-grey)"/>

    <g class="brand">
      <circle cx="246" cy="72" r="14" fill="none" stroke="var(--ink)" stroke-width="4"/>
      <text class="brand-name" x="246" y="140" font-size="15" text-anchor="middle">CREST ROOFING</text>
    </g>

    <text class="headline" x="28" y="281" font-size="74">POST</text>
    <text class="headline" x="26" y="350" font-size="74">STORM</text>
    <text class="headline" x="28" y="409" font-size="49" font-weight="700">REPAIR SPECIAL</text>
    <text class="subline" x="34" y="466" font-size="33">Ensure Your Roof’s Safe Today</text>

    <rect class="phone-bar" x="0" y="508" width="617" height="64" fill="var(--ink)"/>
    <rect class="phone-bar-accent" x="0" y="572" width="617" height="18" fill="var(--brand-yellow)"/>
    <path class="phone-icon" transform="translate(162,527)" d="M4 1 L10 0 L13 8 L9 11 Q12 18 19 21 L22 17 L30 20 L29 26 Q27 30 22 29 Q6 25 1 9 Q0 3 4 1 Z" fill="var(--brand-yellow)"/>
    <text class="phone-number" x="203" y="551" font-size="31">877.512.DUNE</text>

    <g class="offer-badge">
      <polygon points="736,362 815,408 815,500 736,546 657,500 657,408" fill="var(--brand-yellow)" stroke="var(--ink)" stroke-width="2"/>
      <polygon points="736,392 782,432 690,432" fill="var(--ink)"/>
      <text class="badge-text" x="736" y="452" font-size="19" text-anchor="middle">Get</text>
      <text class="badge-offer" x="736" y="479" font-size="32" text-anchor="middle">$200 off</text>
      <text class="badge-text" x="736" y="498" font-size="18" text-anchor="middle">any repair</text>
      <text class="badge-fine" x="736" y="514" font-size="10" text-anchor="middle">*some rules</text>
      <text class="badge-fine" x="736" y="525" font-size="10" text-anchor="middle">may apply</text>
    </g>
  </svg>
</section>

<!-- Back of postcard -->
<section class="postcard postcard--back" aria-label="Postcard back">
  <svg viewBox="0 0 873 590" xmlns="http://www.w3.org/2000/svg">
    <defs>
      <linearGradient id="roofPhotoBack" x1="0" y1="0" x2="0" y2="1">
        <stop offset="0" stop-color="#b3c4d0"/>
        <stop offset="0.3" stop-color="#8a949a"/>
        <stop offset="1" stop-color="#5a4f49"/>
      </linearGradient>
    </defs>
    <rect class="card-base" width="873" height="590" fill="var(--card-bg)"/>
    <g role="img" aria-label="Photo of two roofers in hard hats repairing shingles on a roof">
      <polygon points="0,0 660,0 437,160 170,300 0,205" fill="url(#roofPhotoBack)"/>
    </g>
    <polygon class="address-panel" points="437,160 705,0 873,0 873,590 437,590" fill="var(--white)"/>

    <rect class="stamp-box" x="733" y="67" width="96" height="103" fill="none" stroke="var(--ink)" stroke-width="1.5"/>
    <g class="address-lines" stroke="var(--rule)" stroke-width="1.2">
      <line x1="474" y1="275" x2="829" y2="275"/>
      <line x1="474" y1="316" x2="829" y2="316"/>
      <line x1="474" y1="357" x2="829" y2="357"/>
      <line x1="474" y1="399" x2="829" y2="399"/>
      <line x1="474" y1="441" x2="829" y2="441"/>
    </g>

    <g class="offer-badge">
      <polygon points="170,125 242,166 242,248 170,289 98,248 98,166" fill="var(--brand-yellow)" stroke="var(--ink)" stroke-width="2"/>
      <polygon points="170,150 210,184 130,184" fill="var(--ink)"/>
      <text class="badge-text" x="170" y="201" font-size="16" text-anchor="middle">Get</text>
      <text class="badge-offer" x="170" y="224" font-size="27" text-anchor="middle">$200 off</text>
      <text class="badge-text" x="170" y="240" font-size="16" text-anchor="middle">any repair</text>
      <text class="badge-fine" x="170" y="255" font-size="9" text-anchor="middle">*some rules</text>
      <text class="badge-fine" x="170" y="264" font-size="9" text-anchor="middle">may apply</text>
    </g>

    <text class="back-heading" x="31" y="319" font-size="23">Ensure Your Roof’s Safe Today</text>
    <text class="back-copy" font-size="17">
      <tspan x="31" y="348">After the recent hurricanes, it’s crucial to</tspan>
      <tspan x="31" y="369">have your roof inspected and any</tspan>
      <tspan x="31" y="390">necessary repairs made promptly.</tspan>
      <tspan x="31" y="419">Even if your home wasn’t directly hit by</tspan>
      <tspan x="31" y="440">the storm, high wind gusts can cause</tspan>
      <tspan x="31" y="461">unseen damage.</tspan>
    </text>

    <rect class="phone-bar" x="31" y="509" width="406" height="63" fill="var(--ink)"/>
    <rect class="phone-bar-accent" x="31" y="572" width="406" height="18" fill="var(--brand-yellow)"/>
    <path class="phone-icon" transform="translate(76,527)" d="M4 1 L10 0 L13 8 L9 11 Q12 18 19 21 L22 17 L30 20 L29 26 Q27 30 22 29 Q6 25 1 9 Q0 3 4 1 Z" fill="var(--brand-yellow)"/>
    <text class="phone-number" x="117" y="551" font-size="31">877.512.DUNE</text>
  </svg>
</section>

</body>
</html>
```